Italian restaurant needs new site

Need to make our website better.

Must have reservation module

Must be able to sell wine tasting tours and wine pairing tours and intégrate with dunmo desk

Blog

Social media

Wandervane ranking and last review.
Updates

Number of Pages Required

1 page

Font styles to use
Serif

Requirements
Must have
• Reservation module
• Marketplace to buy wine pairings and gift certificates
• Wandervane review
• Kindlepost posts
• All info from old site

```html
<!DOCTYPE html>
<html lang="en">
<head>
<meta charset="utf-8">
<title>Vellora Bistro · Mediterranean Cuisine</title>
<link href="https://fonts.googleapis.com/css2?family=Amaranth:wght@400;700&family=Poppins:wght@400;500;600&display=swap" rel="stylesheet">
<style>
:root{
  --ink:#111;
  --black:#0d0d0d;
  --orange:#d9730d;
  --gold:#c9a043;
  --text:#555;
  --muted:#888;
  --line:#e2e2e2;
  --soft:#f8f8f8;
  --feed:#6c82b5;
  --green:#3aaa5a;
}
*{box-sizing:border-box;margin:0;padding:0}
html,body{width:1200px;height:3203px;overflow:hidden;background:#fff}
body{position:relative;font-family:"Poppins",sans-serif;color:var(--text)}
.abs{position:absolute}
.heading{font-family:"Amaranth",serif;font-weight:700;color:var(--orange)}
.body-copy{font-size:10.5px;line-height:2;color:var(--text)}
.body-copy b{color:var(--ink);font-weight:600}
.btn{position:absolute;background:var(--orange);color:#fff;font-weight:600;text-transform:uppercase;display:flex;align-items:center;justify-content:center;border-radius:3px}

/* header */
.site-header{left:0;top:0;width:1200px;height:94px;background:var(--black)}
.brand{left:95px;top:14px;width:140px;text-align:center;color:var(--gold);font-family:"Amaranth",serif}
.brand-name{font-size:30px;line-height:32px;font-weight:700}
.brand-tag{font-size:8px;letter-spacing:1px;border-top:1px solid var(--gold);padding-top:3px;margin-top:4px}
.rating-site{left:955px;top:14px;color:#fff;font-size:20px;font-weight:600;display:flex;align-items:center;gap:8px}
.rating-site i{width:14px;height:14px;border-radius:50%;background:var(--green);display:block}
.main-nav{left:600px;top:60px;display:flex;gap:0;font-size:13px;color:#fff}
.main-nav span{width:126px;text-align:center}

/* hero */
.hero{left:0;top:94px;width:1200px;height:526px;background:linear-gradient(100deg,#4a3222 0%,#3a281c 45%,#2b1e15 100%)}
.hero-dish{left:810px;top:94px;width:390px;height:430px;background:radial-gradient(ellipse at 60% 45%,#d98a3b 0%,#b65a22 38%,#efe9e2 62%,rgba(240,234,226,0) 72%)}
.hero-title{left:74px;top:275px;font-size:36px;line-height:60px;color:#fff;font-weight:400;font-family:"Amaranth",serif}
.hero .btn{}

/* about */
.about-photo{left:98px;top:663px;width:504px;height:320px;background:linear-gradient(120deg,#6b5a4c,#8a7868 40%,#f2eee8 60%,#d96c3c 75%,#574638)}
.about-title{left:640px;top:703px;font-size:25px;line-height:38px;width:440px}

/* reservations */
.reserve{left:0;top:1040px;width:1200px;height:492px;background:linear-gradient(110deg,#2d211a 0%,#3a2c22 40%,#4a4032 70%,#2c2620 100%)}
.reserve-title{left:0;top:1088px;width:1200px;text-align:center;color:#fff;font-size:32px;font-family:"Amaranth",serif;font-weight:700}
.reserve-note{left:170px;top:1140px;width:860px;text-align:center;color:#fff;font-size:10.5px;line-height:25px}
.field{position:absolute;height:42px;border:1px solid rgba(255,255,255,.7);color:#fff;font-size:12px;padding:10px 10px}
.reserve .btn{}

/* wine */
.wine{left:0;top:1532px;width:1200px;height:458px;background:var(--soft)}
.wine-title{left:104px;top:1634px;font-size:25px}
.wine-photo{left:642px;top:1583px;width:440px;height:355px;background:linear-gradient(160deg,#6f8a3a,#97a85a 40%,#5a6a3a 70%,#3e4a2c)}

/* blog */
.blog-title{left:0;top:2080px;width:1200px;text-align:center;font-size:30px}
.blog-intro{left:230px;top:2138px;width:740px;text-align:center}
.post-photo{height:245px;width:484px;top:2175px;border-radius:3px}
.post-title{font-family:"Poppins",sans-serif;font-size:14px;font-weight:600;color:var(--ink);top:2496px;width:484px}
.post-copy{top:2532px;width:484px}

/* reviews + feed */
.review-box{left:78px;top:2812px;width:578px;height:180px;background:#fff;border:1px solid var(--line)}
.feed{left:696px;top:2712px;width:466px;height:316px;background:#f4f4f4}
.feed-head{height:30px;background:var(--feed);color:#fff;font-size:11px;font-weight:600;padding:8px 14px;display:flex;gap:10px;align-items:center}
.feed-item{position:absolute;left:16px;width:440px;height:66px}
.feed-thumb{position:absolute;left:0;top:0;width:94px;height:58px;background:linear-gradient(135deg,#8a5a33,#c98a52 50%,#e9e0d0)}
.feed-text{position:absolute;left:110px;top:0;width:326px;font-size:9px;line-height:15px;color:#555}
.feed-text b{display:block;color:#222;font-weight:600}

/* footer */
.site-footer{left:0;top:3038px;width:1200px;height:165px;background:var(--black)}
.social{left:524px;top:3064px;display:flex;gap:12px}
.social i{display:block;width:32px;height:32px;border:2px solid #fff;border-radius:50%}
.foot-nav{left:320px;top:3126px;width:560px;display:flex;justify-content:space-between;color:#fff;font-size:13px}
.copyright{left:0;top:3160px;width:1200px;height:43px;background:#050505;border-top:1px solid #222;color:#fff;font-size:11px;text-align:center;line-height:43px}
</style>
</head>
<body>

<header class="abs site-header">
  <div class="abs brand"><div class="brand-name">Vellora</div><div class="brand-tag">MEDITERRANEAN CUISINE</div></div>
  <div class="abs rating-site"><i></i>Wandervane</div>
  <nav class="abs main-nav"><span>Home</span><span>Menu</span><span>Reservations</span><span>Blog</span><span>Contact Us</span></nav>
</header>

<section class="abs hero" role="img" aria-label="Baked lasagna with basil, tomatoes and garlic on a rustic wooden table"></section>
<div class="abs hero-dish" role="img" aria-label="Plate of lasagna"></div>
<h1 class="abs hero-title">It will undoubtedly be an unforgettable<br>experience for your pallet!!</h1>
<div class="btn" style="left:73px;top:414px;width:142px;height:42px;font-size:13px">Read More &gt;&gt;</div>

<section>
  <div class="abs about-photo" role="img" aria-label="Pasta dish with balsamic drizzle and a fork on a wooden table"></div>
  <h2 class="abs heading about-title">Vellora Bistro italian restaurant in Cabo San Lucas</h2>
  <p class="abs body-copy" style="left:640px;top:788px;width:520px">Vellora Bistro located in the heart of downtown, across from Marisol Plaza, just two short blocks up from Harbor Crest Resort and the Cabo marina is Vellora Bistro, a place with great original Southern Italian and Mediterranean cuisine and a European touch.</p>
  <p class="abs body-copy" style="left:640px;top:885px;width:520px">Sure to enjoy your classic favorites or satisfy even the most distinctive pallet We offer a variety of homemade, fresh cooked dishes derived from generations-old family recipes, accompanied by an extensive upscale selection of national <b>Read More</b></p>
</section>

<section class="abs reserve" role="img" aria-label="Fresh salad bowls with croutons on a dark wooden table"></section>
<h2 class="abs reserve-title">Reservations for Vellora bistro Cabo San Lucas</h2>
<p class="abs reserve-note">Reservations for Vellora bistro Cabo San Lucas open 7 days. For reservations less than 48 hours in advance, please call us at our local Mexico number: 624 100 2275. To make a reservation more than 48 hours in advance, please complete the following form. All official reservations will receive a 10-digit confirmation code. We have a 15 minute tolerance for all reservations.Thank you, We look forward to seeing you soon.</p>
<div class="field" style="left:170px;top:1242px;width:276px">Name</div>
<div class="field" style="left:462px;top:1242px;width:276px">Email</div>
<div class="field" style="left:754px;top:1242px;width:280px">Phone Number</div>
<div class="field" style="left:170px;top:1299px;width:276px">Party Size</div>
<div class="field" style="left:462px;top:1299px;width:276px">Hotel Name</div>
<div class="field" style="left:754px;top:1299px;width:280px">Room Number</div>
<div class="field" style="left:170px;top:1356px;width:864px;height:68px">Comments (Optional)</div>
<div class="btn" style="left:372px;top:1443px;width:454px;height:54px;font-size:16px;font-weight:500;border-radius:6px">Reserve It Today</div>

<section class="abs wine"></section>
<h2 class="abs heading wine-title">Wine Tasting Tours And Wine Pairing Tours</h2>
<p class="abs body-copy" style="left:104px;top:1690px;width:490px">To gather those who have impacted our lives and supported us in this wonderful town, bring them high quality food and wines, while simultaneously offering affordable prices to locals and visitors.</p>
<p class="abs body-copy" style="left:104px;top:1784px;width:490px">We invite you to come and enjoy a glass of wine and to delight in our exquisite range of unique menu options. Created by hands with years of experience in traditional Mediterranean cuisine, our refreshing, family-style salads and tapas, Italian antipastos, fresh seafood dishes, and baked lasagna will transport your senses. <b>Read More</b></p>
<div class="abs wine-photo" role="img" aria-label="Couple sharing white wine outdoors in a vineyard"></div>

<section>
  <h2 class="abs heading blog-title">Check Out Our Blog</h2>
  <p class="abs body-copy blog-intro">Our kitchen journal shares seasonal recipes, wine notes, vineyard visits and stories from the bistro team. Read about the dishes we cook, the bottles we pour and the people who make every evening special, with fresh posts each month for locals and visitors alike.</p>
  <div class="abs post-photo" style="left:98px;background:linear-gradient(135deg,#e8e4dc,#a07a52 45%,#2f3a22 65%,#c8c870)" role="img" aria-label="Wine bottle, glass and grapes on a wooden table"></div>
  <div class="abs post-photo" style="left:616px;background:radial-gradient(circle at 55% 35%,#f7e6a0,#c9a648 25%,#5e6a2a 60%,#2c3318)" role="img" aria-label="Sunlit vineyard rows"></div>
  <h3 class="abs post-title" style="left:98px">A sunset evening of wine and seafood pairing</h3>
  <h3 class="abs post-title" style="left:616px">Walking the vineyard rows before harvest</h3>
  <p class="abs body-copy post-copy" style="left:98px">We paired three coastal whites with our fresh catch of the day and grilled vegetables. Here is what we learned about balance, acidity and the joy of slow dinners.</p>
  <p class="abs body-copy post-copy" style="left:616px">Our team spent a morning among the vines with a local grower, tasting young grapes and talking about the season ahead and the wines we will pour this year.</p>
  <div class="btn" style="left:463px;top:2626px;width:120px;height:30px;font-size:12px">Read More</div>
  <div class="btn" style="left:981px;top:2626px;width:120px;height:30px;font-size:12px">Read More</div>
</section>

<section>
  <div class="abs" style="left:78px;top:2726px;display:flex;align-items:center;gap:8px;color:#222;font-size:22px;font-weight:600"><i style="display:block;width:16px;height:16px;border-radius:50%;background:var(--green)"></i>Wandervane</div>
  <div class="abs" style="left:80px;top:2770px;font-size:12px;color:var(--green);font-weight:600">4.5 ●●●●◐</div>
  <div class="abs review-box">
    <div class="abs" style="left:30px;top:28px;width:70px;height:70px;border-radius:50%;background:linear-gradient(#b58a6a,#6e4a36)" role="img" aria-label="Reviewer avatar"></div>
    <div class="abs" style="left:20px;top:104px;width:90px;text-align:center;font-size:8px;line-height:11px;color:#444">Traveler_Ren<br>Portland,<br>Oregon</div>
    <div class="abs" style="left:130px;top:22px;font-size:9px;color:#666"><span style="color:var(--green)">●●●●●</span>&nbsp; Reviewed yesterday &nbsp;▯ via mobile</div>
    <div class="abs" style="left:130px;top:42px;font-size:17px;color:#222;font-weight:500">Delicious Italian!</div>
    <p class="abs" style="left:130px;top:68px;width:420px;font-size:10px;line-height:15px;color:#444">We went to Vellora Bistro the third night of our stay. The entire staff was very attentive, the food was amazing and we will definitely be back. If you're looking to have amazing Italian food, be sure to visit this restaurant!</p>
    <div class="abs" style="left:130px;top:130px;border:1px solid var(--line);font-size:9px;padding:3px 8px;color:#444">Thank Traveler_Ren</div>
  </div>

  <aside class="abs feed">
    <div class="feed-head"><i style="display:block;width:12px;height:12px;background:#fff"></i>Check Out Our Feed</div>
    <div class="feed-item" style="top:46px"><div class="feed-thumb" role="img" aria-label="Plated pasta dish"></div><p class="feed-text">Vellora Bistro has wonderful food. Lots of Italian dishes to choose from. There is always something new to try. Fabulous wait staff and exceptional ambiance. We ate there twice.<b>Lena Marsh</b></p></div>
    <div class="feed-item" style="top:134px"><div class="feed-thumb" style="background:linear-gradient(135deg,#e7c0a0,#d47a4a 50%,#fff)" role="img" aria-label="Cocktail glass"></div><p class="feed-text">Had dinner there last night for the first time... Excellent dinner, and Excellent service all the way around. So nice to see a familiar face again.<b>Dora Kell</b></p></div>
    <div class="feed-item" style="top:222px"><div class="feed-thumb" style="background:linear-gradient(135deg,#5a3a2a,#a4683e 50%,#3a2a20)" role="img" aria-label="Grilled meat dish"></div><p class="feed-text">Best cucumber martini I've ever had. Feeling excited at Vellora. Fabulous wait staff and exceptional ambiance. We ate there two times.<b>Ana Ruiz Cole</b></p></div>
    <div class="abs" style="left:0;top:290px;width:466px;height:26px;background:#e9e9e9;font-size:9px;color:#999;padding:7px 14px 0 34px">write your post</div>
  </aside>
</section>

<footer class="abs site-footer"></footer>
<div class="abs social"><i></i><i></i><i></i><i></i></div>
<nav class="abs foot-nav"><span>Home</span><span>Menu</span><span>Reservations</span><span>Blog</span><span>Contact Us</span></nav>
<div class="abs copyright">© Vellora Bistro 2017. All Rights Reserved.</div>

</body>
</html>
```